Logo, Web and Mobile Designs for enterprise social media platform

All the details are in the attached document, please start reading the scope document first which explains what is this project about and the details about the needed deliverables, after that please read the UI_Requirements document which will detail what is expected regarding the coded web version since this is a coded contest, it is very important that you meet the UI requirements or suggest something else but we will need to agree first before working on the coded version

Good Luck

Target Market(s)

Enterprise Social Media

Industry/Entity Type

Media

Coding

Coded - Design and coding required

Number of Pages Required

5+ page

Font styles to use
Sans Serif

Requirements
Must have
• All the must haves are listed in the scope document so please check before you start

```html
<!DOCTYPE html>
<html lang="en">
<head>
<meta charset="utf-8">
<title>Teamora – Exhibitor Details</title>
<link href="https://fonts.googleapis.com/css2?family=Roboto:wght@400;500&display=swap" rel="stylesheet">
<style>
:root{
  --brand:#1e8bc3;
  --brand-dark:#1578b0;
  --accent:#f7a21b;
  --page:#ebebeb;
  --panel:#ffffff;
  --side:#f3f3f3;
  --line:#e2e2e2;
  --text:#555555;
  --muted:#8a8a8a;
  --footer:#1e8bb8;
  --white:#ffffff;
}
*{box-sizing:border-box;margin:0;padding:0}
html,body{width:1200px;height:826px;overflow:hidden}
body{font-family:'Roboto',sans-serif;background:var(--page);color:var(--text);position:relative}
.abs{position:absolute}

/* header */
.topbar{position:absolute;left:0;top:0;width:1200px;height:70px;background:#fafafa;border-bottom:1px solid #dcdcdc}
.topbar .menu-btn{left:101px;top:29px}
.topbar .divider{position:absolute;top:0;width:1px;height:70px;background:var(--line)}
.brand-mark{left:168px;top:15px;width:40px;height:40px;border-radius:50%;background:var(--accent)}
.brand-name{left:221px;top:16px;font-size:31px;font-weight:500;color:var(--brand);letter-spacing:.3px}
.avatar{left:746px;top:20px;width:34px;height:34px;border-radius:50%;background:radial-gradient(circle at 50% 40%,#8a7b70,#2f2a27)}
.user-name{left:793px;top:27px;font-size:16px;color:var(--text)}
.caret{left:888px;top:34px}
.badge{position:absolute;width:20px;height:16px;border-radius:8px;font-size:11px;color:var(--white);text-align:center;line-height:16px}
.badge.orange{background:var(--accent);left:957px;top:16px}
.badge.blue{background:#1e9ad6;left:1079px;top:16px}

/* panel */
.panel{left:99px;top:105px;width:1001px;height:534px;background:var(--panel);border:1px solid #dcdcdc}
.sidebar{position:absolute;left:0;top:0;width:278px;height:532px;background:var(--side);border-right:1px solid #dcdcdc}
.side-main{position:absolute;left:0;width:278px;height:54px;border-bottom:1px solid var(--line);display:flex;align-items:center;padding-left:46px;font-size:15.5px;color:#444}
.side-main svg{position:absolute;left:17px}
.side-link{position:absolute;left:0;width:278px;height:32px;border-bottom:1px solid var(--line);font-size:16px;color:#666;padding-left:42px;line-height:30px}
.side-link::before{content:"";position:absolute;left:19px;top:12px;width:6px;height:6px;border-top:1.5px solid #666;border-right:1.5px solid #666;transform:rotate(45deg)}
.side-link.active{color:var(--brand)}

.card{position:absolute;left:310px;top:40px;width:660px;height:427px;border:1px solid #e6e6e6;background:var(--white)}
.card-head{height:50px;background:#f5f6f8;border-bottom:1px solid #e3e3e3;position:relative}
.card-title{position:absolute;left:49px;top:17px;font-size:15.5px;color:#555}
.card-head svg{position:absolute;left:26px;top:17px}
.field-label{position:absolute;left:22px;font-size:15px;color:#666}
.field{position:absolute;left:186px;width:451px;height:39px;border:1px solid #dedede;font-size:11px;color:#444;padding-left:18px;line-height:37px}
.file-name{position:absolute;left:208px;top:281px;font-size:13px;color:#555}
.add-btn{position:absolute;left:185px;top:313px;width:171px;height:35px;background:var(--brand);border-bottom:2px solid var(--brand-dark);border-radius:2px;color:var(--white);font-size:16px;font-weight:500;text-align:center;line-height:34px;letter-spacing:.3px}
.list-dot{position:absolute;left:19px;top:391px;width:15px;height:15px;border-radius:50%;background:var(--brand)}
.list-name{position:absolute;left:40px;top:392px;font-size:11px;color:#444}

/* footer */
.footer{position:absolute;left:0;top:679px;width:1200px;height:147px;background:var(--footer);color:var(--white);text-align:center}
.social{position:absolute;top:28px;left:513px;display:flex;gap:13px}
.social span{width:24px;height:24px;border-radius:4px;background:var(--white);display:block}
.foot-links{position:absolute;top:71px;width:100%;font-size:14.5px}
.foot-links .sep{margin:0 9px}
.copyright{position:absolute;top:101px;width:100%;font-size:14px;font-weight:500}
</style>
</head>
<body>

<header class="topbar">
  <svg class="abs menu-btn" width="18" height="14" viewBox="0 0 18 14"><g fill="#888"><rect width="18" height="2.5"/><rect y="5.7" width="18" height="2.5"/><rect y="11.4" width="18" height="2.5"/></g></svg>
  <span class="divider" style="left:144px"></span>
  <div class="abs brand-mark"></div>
  <div class="abs brand-name">Teamora</div>
  <div class="abs avatar" role="img" aria-label="User profile photo"></div>
  <div class="abs user-name">Dana Pirell</div>
  <svg class="abs caret" width="11" height="7" viewBox="0 0 11 7"><path d="M0 0h11L5.5 7z" fill="#555"/></svg>
  <span class="divider" style="left:922px"></span>
  <svg class="abs" style="left:946px;top:27px" width="20" height="18" viewBox="0 0 20 18"><g fill="#777"><rect width="12" height="4"/><rect y="7" width="20" height="4"/><rect y="14" width="8" height="4"/><rect x="10" y="14" width="10" height="4" fill="#bbb"/></g></svg>
  <span class="badge orange">8</span>
  <span class="divider" style="left:991px"></span>
  <svg class="abs" style="left:1012px;top:26px" width="20" height="20" viewBox="0 0 20 20"><circle cx="8" cy="8" r="6" fill="none" stroke="#777" stroke-width="2.6"/><path d="M12.5 12.5L18 18" stroke="#777" stroke-width="3" stroke-linecap="round"/></svg>
  <span class="divider" style="left:1051px"></span>
  <svg class="abs" style="left:1072px;top:27px" width="19" height="20" viewBox="0 0 19 20"><path d="M9.5 1c-3.5 0-5.5 2.6-5.5 6v5l-2.5 3h16L15 12V7c0-3.4-2-6-5.5-6z" fill="#777"/><circle cx="9.5" cy="17.5" r="2.2" fill="#777"/></svg>
  <span class="badge blue">8</span>
</header>

<main class="abs panel">
  <nav class="sidebar">
    <div class="side-main" style="top:0">
      <svg width="15" height="13" viewBox="0 0 15 13"><g fill="#1e8bc3"><rect width="6.5" height="5.5" rx="1"/><rect x="8" width="7" height="5.5" rx="1"/><rect y="7" width="6.5" height="6" rx="1"/><rect x="8" y="7" width="7" height="6" rx="1"/></g></svg>
      VIEW DASHBOARD
    </div>
    <div class="side-main" style="top:55px">
      <svg width="15" height="15" viewBox="0 0 15 15"><rect x="0.5" y="2" width="14" height="12.5" rx="1" fill="none" stroke="#1e8bc3" stroke-width="1.4"/><rect x="0.5" y="2" width="14" height="3" fill="#1e8bc3"/><g fill="#1e8bc3"><rect x="3" y="7" width="2" height="2"/><rect x="6.5" y="7" width="2" height="2"/><rect x="10" y="7" width="2" height="2"/><rect x="3" y="10.5" width="2" height="2"/><rect x="6.5" y="10.5" width="2" height="2"/><rect x="10" y="10.5" width="2" height="2"/></g><rect x="3.5" y="0" width="1.5" height="3.5" fill="#1e8bc3"/><rect x="10" y="0" width="1.5" height="3.5" fill="#1e8bc3"/></svg>
      VIEW EVENT
    </div>
    <div class="side-link" style="top:129px">About Us</div>
    <div class="side-link" style="top:161px">Speakers</div>
    <div class="side-link" style="top:194px">Track</div>
    <div class="side-link" style="top:226px">Sessions</div>
    <div class="side-link" style="top:259px">Tickets</div>
    <div class="side-link" style="top:292px">Organizers</div>
    <div class="side-link" style="top:324px">Sponsors</div>
    <div class="side-link active" style="top:357px">EXHIBITOR</div>
    <div class="side-link" style="top:389px">Security</div>
    <div class="side-link" style="top:422px">Members</div>
  </nav>

  <section class="card">
    <div class="card-head">
      <svg width="16" height="16" viewBox="0 0 16 16"><path d="M1 7h3v8H1zM5 14.5V7.5L8.5 1.5c1.3 0 2 .8 1.8 2L9.7 6H14c1 0 1.7.9 1.5 1.8l-1.2 5.8c-.2.8-.8 1.3-1.6 1.3H5z" fill="none" stroke="#666" stroke-width="1.3" stroke-linejoin="round"/></svg>
      <div class="card-title">EXHIBITOR DETAILS</div>
    </div>
    <div class="field-label" style="top:102px">Exhibitor Name :</div>
    <div class="field" style="top:84px">Corvex</div>
    <div class="field-label" style="top:154px">Booth Number :</div>
    <div class="field" style="top:135px">20</div>
    <div class="field-label" style="top:205px">Booth Location :</div>
    <div class="field" style="top:186px">Room1</div>
    <div class="field-label" style="top:254px;left:18px">Upload Exhibitor Photo :</div>
    <svg class="abs" style="left:189px;top:256px" width="18" height="13" viewBox="0 0 18 13"><path d="M4.5 13A4 4 0 0 1 4 5a5.5 5.5 0 0 1 10.5 1A3.5 3.5 0 0 1 14 13z" fill="#1e8bc3"/><path d="M9 4.5l3 3H10v3H8v-3H6z" fill="#fff"/></svg>
    <svg class="abs" style="left:183px;top:282px" width="17" height="13" viewBox="0 0 17 13"><rect x="0.5" y="0.5" width="16" height="12" fill="none" stroke="#888"/><path d="M2 11l4-5 3 3 2-2 4 4z" fill="#888"/><circle cx="12" cy="4" r="1.5" fill="#888"/></svg>
    <div class="file-name">Corvex-logo.png</div>
    <div class="add-btn">ADD EXHIBITOR</div>
    <div class="field-label" style="top:364px;left:19px">Exhibitor List :</div>
    <div class="list-dot"></div>
    <div class="list-name">Corvex</div>
  </section>
</main>

<footer class="footer">
  <div class="social"><span></span><span></span><span></span><span></span><span></span></div>
  <div class="foot-links">Home<span class="sep">/</span>Contact<span class="sep">/</span>Topics<span class="sep">/</span>Posts and Comments<span class="sep">/</span>Discussion<span class="sep">/</span>Videos Links</div>
  <div class="copyright">Copyright @ 2015 - 2015.Teamora. All Rights Reserved.</div>
</footer>

</body>
</html>
```